Business Card Design Project

We need a business card for a new technology services company. We develop software and implement software packages for our business customers and although we will begin with just one or two service offerings, our service offerings will expand over time. Our name comes from the an author, KL Barrow, and his "idea" was that opportunity should be based on ability and achievement, not on social status.

We would like to see a design that is standard in its size and shape, but stands apart in its dramatic color contrasts. The card should not use too many colors - the colors used in the background should highlight the brilliant blues of the logo (see attachment) to dramatic effect. The background should not be white.

If necessary, you can change the color of the words "KL Barrow", but not the word "Idea".

Card size should be U.S. standard 2 inches by 3.5 inches and provide for 1/8 inch bleed area on each side.

We need a design for both sides of the business card, one side communicating the company logo and contact information, the other side being purely graphical, incorporating the logo but no other information.

Contact Information Required:
Kate Brook
KateBrook@klbarrowvista.com
614-387-2259

Target Market(s)

Business executives

Industry/Entity Type

Software

Requirements
Must have
• It must have the full company logo on one side, and at least the graphic element of the logo on the other. Either that or the full logo on both.
Nice to have
• It would be nice to have a design that could work without needing two different textures. For example, it would be nice if the entire card could be shiny, not just parts of the card.

It would also be nice if texture is something we could add later.
Should not have
• The card should not use the color green.

```html
<!DOCTYPE html>
<html lang="en">
<head>
<meta charset="utf-8">
<title>KL Barrow Vista — Business Card</title>
<link rel="stylesheet" href="https://fonts.googleapis.com/css2?family=Arimo:wght@400;700&display=swap">
<style>
  :root {
    --stage: #e9eaee;
    --card-dark: #2c2d31;
    --card-mid: #55585e;
    --ink-light: #f2f3f5;
    --blue: #1aa3e0;
    --blue-deep: #0a6fb3;
    --swoosh-grey: #a9acb1;
    --swoosh-dark: #3a3b40;
  }
  * { box-sizing: border-box; margin: 0; padding: 0; }
  html, body { width: 1200px; height: 987px; overflow: hidden; }
  body {
    background: var(--stage);
    font-family: "Arimo", Arial, sans-serif;
    position: relative;
  }
  .card {
    position: absolute;
    width: 700px;
    height: 400px;
    border-radius: 28px;
    overflow: hidden;
    background: radial-gradient(ellipse at 55% 30%, var(--card-mid) 0%, var(--card-dark) 75%);
  }
  .card--back { left: 440px; top: 60px; }
  .card--front { left: 70px; top: 520px; }

  .wordmark {
    display: flex;
    align-items: center;
    gap: 18px;
    color: var(--ink-light);
    font-weight: 700;
    letter-spacing: 0.5px;
    white-space: nowrap;
  }
  .wordmark__dot {
    border-radius: 50%;
    background: var(--blue);
    flex: none;
  }

  .card--back .wordmark {
    position: absolute;
    left: 60px;
    top: 166px;
    font-size: 54px;
  }
  .card--back .wordmark__dot { width: 56px; height: 56px; }

  .card--front .wordmark {
    position: absolute;
    left: 46px;
    top: 50px;
    font-size: 38px;
  }
  .card--front .wordmark__dot { width: 38px; height: 38px; }

  .contact {
    position: absolute;
    left: 48px;
    top: 122px;
    list-style: none;
    color: var(--ink-light);
    font-size: 19px;
    line-height: 32px;
  }
  .contact li { display: flex; align-items: center; gap: 10px; }
  .contact svg { width: 16px; height: 16px; flex: none; }

  .swoosh { position: absolute; left: 0; top: 0; width: 700px; height: 400px; }

  .holder-name {
    position: absolute;
    right: 48px;
    bottom: 34px;
    color: var(--ink-light);
    font-weight: 700;
    font-size: 34px;
    letter-spacing: 1px;
  }
</style>
</head>
<body>

  <section class="card card--back" aria-label="Card back">
    <div class="wordmark"><span>KL Barrow Vista</span><span class="wordmark__dot"></span></div>
  </section>

  <section class="card card--front" aria-label="Card front">
    <svg class="swoosh" viewBox="0 0 700 400" aria-hidden="true">
      <defs>
        <linearGradient id="blueBand" x1="0" y1="0" x2="1" y2="0">
          <stop offset="0" stop-color="#22b0ec"/>
          <stop offset="1" stop-color="#0b78bf"/>
        </linearGradient>
      </defs>
      <path d="M0 240 C120 250 220 300 330 320 C440 340 560 330 700 360 L700 400 L0 400 Z" fill="var(--swoosh-grey)"/>
      <path d="M0 262 C140 272 230 312 340 332 C460 352 580 340 700 372 L700 400 L0 400 Z" fill="var(--swoosh-dark)"/>
      <path d="M0 236 C150 252 260 300 360 316 C480 334 600 322 700 340" fill="none" stroke="var(--blue)" stroke-width="4"/>
      <path d="M40 400 C120 330 220 310 330 322 C450 336 580 300 700 318 L700 400 Z" fill="url(#blueBand)"/>
    </svg>

    <div class="wordmark"><span>KL Barrow Vista</span><span class="wordmark__dot"></span></div>

    <ul class="contact">
      <li>
        <svg viewBox="0 0 16 16" aria-hidden="true"><circle cx="8" cy="8" r="8" fill="var(--blue)"/><path d="M5.2 4.2l1.4 1.4-.8 1c.6 1.2 1.4 2 2.6 2.6l1-.8 1.4 1.4-1 1.1C7.4 10.9 5.1 8.6 4.1 5.2z" fill="#fff"/></svg>
        <span>614-387-2259</span>
      </li>
      <li>
        <svg viewBox="0 0 16 16" aria-hidden="true"><rect x="1" y="3" width="14" height="10" rx="1.5" fill="var(--blue)"/><path d="M1.5 4l6.5 5 6.5-5" fill="none" stroke="#fff" stroke-width="1.4"/></svg>
        <span>KateBrook@klbarrowvista.com</span>
      </li>
    </ul>

    <div class="holder-name">KATE BROOK</div>
  </section>

</body>
</html>
```